Trinkets & Novelties: Promotional Products and Apparel- Tri fold hand out

Promotional Products / Advertising Specialties distributor with in-house manufacturing capabilities. We want to improve our Tri-Fold hand out that we use for Tradeshows and new customers.
Our old Tri-fold is attached. I don't care for the layout and much of the content, so I would use it as an example of how not to do the new tri-fold. Our business card is attached and I'd like the color scheme of the new tri-fold to match the color scheme of the business card. Our logo is attached and a word doc is attached for the content / text of the new tri-fold. Tri-fold should use a combination of pictures and text. Front cover should clearly define Promotional Products and Corporate Apparel.

Target Market(s)

Corporate Business

Industry/Entity Type

Advertising

Colors
3176b5

Requirements
Must have
• company name, phone, address, web
Nice to have
• Pics of screen printing, embroidery equipment
Should not have
• n/a

```html
<!DOCTYPE html>
<html lang="en">
<head>
<meta charset="utf-8">
<title>Trinkets &amp; Novelties – Tri-fold Handout</title>
<link href="https://fonts.googleapis.com/css2?family=Hind:wght@400;500;600;700&display=swap" rel="stylesheet">
<style>
  :root {
    --brand-blue: #3176b5;
    --sky-blue: #3a8fd1;
    --navy: #1f4a96;
    --text-grey: #6a6f75;
    --paper: #f7f8f9;
    --paper-fold: #eceef0;
    --backdrop: #9b9d9f;
    --white: #ffffff;
  }
  * { box-sizing: border-box; margin: 0; padding: 0; }
  html, body { width: 1200px; height: 800px; overflow: hidden; }
  body {
    background: var(--backdrop);
    font-family: "Hind", Arial, sans-serif;
    position: relative;
  }
  .trifold {
    position: absolute;
    left: 120px; top: 40px;
    width: 960px; height: 720px;
    display: flex;
    box-shadow: 0 6px 18px rgba(0,0,0,.25);
  }
  .panel {
    position: relative;
    width: 320px; height: 720px;
    background: var(--paper);
    overflow: hidden;
  }
  .panel + .panel { border-left: 1px solid var(--paper-fold); }

  /* Left panel */
  .uses-title {
    position: absolute; left: 40px; top: 52px;
    color: var(--sky-blue);
    font-size: 21px; font-weight: 500; line-height: 22px;
    text-transform: uppercase;
  }
  .uses-title .small { font-size: 18px; }
  .title-rule {
    position: absolute; left: 40px; top: 104px;
    width: 262px; height: 4px;
    background: linear-gradient(90deg, var(--navy), var(--sky-blue));
  }
  .uses-list {
    position: absolute; left: 40px; top: 130px;
    list-style: none;
  }
  .uses-list li {
    display: flex; align-items: center;
    height: 26.5px;
    color: var(--sky-blue);
    font-size: 15px; font-weight: 500;
  }
  .uses-list li::before {
    content: "";
    width: 7px; height: 7px;
    border: 1.5px solid var(--navy);
    border-radius: 50%;
    box-shadow: inset 0 0 0 1.5px var(--paper), inset 0 0 0 4px var(--navy);
    margin-right: 17px;
  }
  .stats-band { position: absolute; left: 0; bottom: 0; width: 320px; height: 320px; }
  .stats-copy {
    position: absolute; left: 44px; right: 30px; top: 476px;
    color: var(--white);
    font-size: 12.5px; line-height: 17.5px;
    text-align: justify;
  }
  .stats-source { margin-top: 18px; }

  /* Middle panel */
  .middle { padding: 66px 30px 0 34px; color: var(--text-grey); }
  .body-copy { font-size: 11.8px; line-height: 20px; text-align: justify; }
  .apart-title {
    margin-top: 32px;
    color: var(--sky-blue);
    font-size: 17px; font-weight: 500; line-height: 19px;
  }
  .feature { margin-top: 16px; }
  .feature h3 { color: var(--sky-blue); font-size: 12.5px; font-weight: 600; line-height: 16px; }
  .feature p { font-size: 11.8px; line-height: 20px; text-align: justify; margin-top: 2px; }
  .contact-block {
    position: absolute; left: 24px; top: 612px;
    display: flex; align-items: center; gap: 12px;
  }
  .contact-name { display: flex; align-items: center; gap: 5px; color: var(--navy); font-size: 11px; font-weight: 700; line-height: 11px; width: 104px; }
  .contact-name .mark { width: 26px; height: 26px; border: 1.5px solid var(--navy); border-radius: 50%; flex: none; }
  .contact-address { font-size: 7.2px; line-height: 10px; color: #333; }
  .social-row {
    position: absolute; left: 24px; top: 676px;
    display: flex; align-items: center; gap: 22px;
    font-size: 8.5px; color: var(--text-grey);
  }
  .social-handle { display: flex; align-items: center; gap: 5px; }
  .social-handle .dot { width: 10px; height: 10px; border-radius: 50%; background: var(--sky-blue); }
  .web-pill {
    background: var(--sky-blue); color: var(--white);
    padding: 2px 8px; font-size: 8.5px;
  }

  /* Right panel */
  .cover-photo { position: absolute; left: 0; top: 0; }
  .brand-mark {
    position: absolute; left: 90px; top: 388px;
    width: 140px; height: 140px;
    border: 3px solid var(--navy);
    border-radius: 50%;
    display: flex; align-items: center; justify-content: center;
    text-align: center;
    color: var(--navy);
    font-size: 17px; font-weight: 700; line-height: 20px;
  }
  .cover-line {
    position: absolute; left: 0; right: 0; top: 552px;
    text-align: center;
    color: var(--sky-blue);
    font-size: 13px; letter-spacing: .3px;
  }
  .cover-tagline {
    position: absolute; left: 0; right: 0; top: 578px;
    text-align: center;
    color: #222; font-size: 13.5px; font-weight: 700;
  }
  .cover-web {
    position: absolute; left: 0; right: 0; top: 632px;
    text-align: center;
    color: var(--sky-blue); font-size: 12px;
  }
</style>
</head>
<body>
  <main class="trifold">
    <section class="panel uses-panel">
      <h2 class="uses-title">Top uses <span class="small">for</span><br>Promotional products</h2>
      <div class="title-rule"></div>
      <ul class="uses-list">
        <li>Brand awareness</li>
        <li>Tradeshows</li>
        <li>New customer / account generation</li>
        <li>Dealer/distributor programs</li>
        <li>Public relation</li>
        <li>Executive Gifts</li>
        <li>Not-for-profit programs</li>
        <li>New product/service introduction</li>
        <li>Employee Excellent Recognition</li>
        <li>Customer referrals</li>
      </ul>
      <svg class="stats-band" viewBox="0 0 320 320" aria-hidden="true">
        <path d="M0 52 Q150 -40 320 58 L320 320 L0 320 Z" fill="var(--sky-blue)"/>
      </svg>
      <div class="stats-copy">
        <p>Gifts That Keep On Giving 58% of respondents keep a promotional product anywhere from one year to more than four years. Even if the recipient uses the item only once per week, that's a minimum of 52 impressions made over the course of a year, with the possibility of more than 208 during that time.</p>
        <p class="stats-source">Source: PMIC Study of the Effectiveness of Promotional Products as an Advertising Medium</p>
      </div>
    </section>

    <section class="panel middle">
      <p class="body-copy">The internet is great for finding you the cheapest product. If your intention is promote yourself by the cheapest means possible continue using the internet. IF you are interested in maximizing your advertising budget by finding the best possible products to meet your intended advertising market, the, please call or email Trinkets &amp; Novelties.</p>
      <h2 class="apart-title">What sets us apart<br>from our competition?</h2>
      <div class="feature">
        <h3>In-House production capability</h3>
        <p>direct from our facility to yours- we reduce cost, and turn around time without sacrificing quality.</p>
      </div>
      <div class="feature">
        <h3>Industry Experience</h3>
        <p>for over 35 years we've been serving our customer with the finest promotional marketing service. We've got the experience to assist you in selecting the proper promotional products.</p>
      </div>
      <div class="feature">
        <h3>Custom Design and Manufacturing</h3>
        <p>need a custom, never before seen promotional product. Let our design team create the perfect product for your organization.</p>
      </div>
      <div class="contact-block">
        <div class="contact-name"><span class="mark"></span>Trinkets &amp; Novelties</div>
        <address class="contact-address" style="font-style:normal">
          SDVOB – Service Disabled Veteran Owned Business<br>
          Trinkets &amp; Novelties<br>
          48 Harbor Lane<br>
          Suite 210 Millbrook NJ 08099<br>
          phone: 555-014-2200 &nbsp;fax: 555-014-2201
        </address>
      </div>
      <div class="social-row">
        <span class="social-handle"><span class="dot"></span>trinketsnov</span>
        <span class="social-handle"><span class="dot"></span>trinketsnov</span>
        <span class="web-pill">www.trinketsapparel.com</span>
      </div>
    </section>

    <section class="panel cover">
      <svg class="cover-photo" width="320" height="380" viewBox="0 0 320 380">
        <defs>
          <linearGradient id="pressTones" x1="0" y1="0" x2="1" y2="1">
            <stop offset="0" stop-color="#d9d4c8"/>
            <stop offset=".45" stop-color="#5d79b8"/>
            <stop offset=".75" stop-color="#d8434a"/>
            <stop offset="1" stop-color="#9aa3ab"/>
          </linearGradient>
        </defs>
        <circle cx="250" cy="150" r="222" fill="var(--navy)"/>
        <circle cx="256" cy="146" r="212" fill="var(--sky-blue)"/>
        <circle cx="262" cy="140" r="196" fill="var(--paper)"/>
        <circle cx="262" cy="140" r="190" fill="url(#pressTones)" role="img" aria-label="Photo of a carousel screen printing press printing red event t-shirts"/>
      </svg>
      <div class="brand-mark">Trinkets &amp;<br>Novelties</div>
      <p class="cover-line">PROMOTIONAL PRODUCTS &amp; APPAREL</p>
      <p class="cover-tagline">Good Products From Good People</p>
      <p class="cover-web">www.trinketsnov.com</p>
    </section>
  </main>
</body>
</html>
```